Brightmill Data Works

Our company is about IT hardwares and IT solutions. IT hardware such as PC, RAMS, storage and servers. IT solutions such as project management, BA. We are also selling new technology too.

Target Market(s)

Consumer, Small to Medium Business, Corporate

Requirements
Must have
• The business card must have the following:
• Name:
• Title:
• Contact Number:
• Email address:
• Website:
• Color: Must match the logo color upgrade

```html
<!DOCTYPE html>
<html lang="en">
<head>
<meta charset="utf-8">
<title>Brightmill Data Works – Business Card</title>
<link href="https://fonts.googleapis.com/css2?family=Lato:wght@400;700;900&display=swap" rel="stylesheet">
<style>
  :root {
    --bg: #1c1c1c;
    --card-dark: #141414;
    --card-light: #ffffff;
    --orange: #e08f25;
    --graphite: #3f3f42;
    --ink: #3a3a3a;
  }
  html, body {
    margin: 0;
    width: 1200px;
    height: 900px;
    overflow: hidden;
    background: var(--bg);
    font-family: "Lato", sans-serif;
  }
  .canvas { position: relative; width: 1200px; height: 900px; }

  .card {
    position: absolute;
    width: 560px;
    height: 320px;
    border-radius: 16px;
    overflow: hidden;
  }
  .card-edge { position: absolute; left: 0; bottom: 0; width: 560px; height: 40px; }

  .wordmark {
    position: absolute;
    left: 0; right: 0;
    display: flex; align-items: center; justify-content: center; gap: 12px;
  }
  .wordmark-dot { width: 24px; height: 24px; border-radius: 50%; background: var(--orange); flex: none; }
  .wordmark-name {
    font-weight: 900; letter-spacing: 1px; text-transform: uppercase; white-space: nowrap;
  }

  /* Front */
  .card--front { left: 90px; top: 90px; background: var(--card-dark); }
  .card--front .wordmark { top: 118px; }
  .card--front .wordmark-name { color: #ffffff; font-size: 32px; }

  /* Back */
  .card--back { left: 550px; top: 490px; background: var(--card-light); }
  .card--back .wordmark { top: 56px; }
  .card--back .wordmark-dot { width: 20px; height: 20px; }
  .card--back .wordmark-name { color: var(--graphite); font-size: 24px; }

  .person { position: absolute; right: 34px; top: 124px; text-align: right; }
  .person-name { color: var(--orange); font-weight: 700; font-size: 22px; margin: 0; line-height: 1.2; }
  .person-title { color: var(--ink); font-size: 14px; margin: 4px 0 0; }

  .contact-tab {
    position: absolute; left: 0; top: 168px;
    width: 54px; height: 128px;
    background: var(--orange);
    border-radius: 0 22px 22px 0;
    display: flex; flex-direction: column; align-items: center; justify-content: center; gap: 10px;
  }
  .contact-tab svg { width: 16px; height: 16px; display: block; }
  .contact-list {
    position: absolute; left: 74px; top: 176px;
    margin: 0; padding: 0; list-style: none;
    color: var(--ink); font-size: 14px; line-height: 26.5px;
  }
</style>
</head>
<body>
<main class="canvas">

  <section class="card card--front" aria-label="Business card front">
    <div class="wordmark">
      <span class="wordmark-dot"></span>
      <span class="wordmark-name">Brightmill Data Works</span>
    </div>
    <svg class="card-edge" viewBox="0 0 560 40" preserveAspectRatio="none">
      <path d="M0 30 H330 Q338 30 342 22 L346 16 Q350 8 360 8 H560 V40 H0 Z" fill="var(--graphite)"/>
      <path d="M336 40 L344 24 Q350 14 362 14 H560 V40 Z" fill="var(--orange)"/>
    </svg>
  </section>

  <section class="card card--back" aria-label="Business card back">
    <div class="wordmark">
      <span class="wordmark-dot"></span>
      <span class="wordmark-name">Brightmill Data Works</span>
    </div>

    <div class="person">
      <p class="person-name">Daniel Marsh</p>
      <p class="person-title">Owner / Founder</p>
    </div>

    <div class="contact-tab">
      <svg viewBox="0 0 16 16" aria-label="Phone"><path d="M4 1.5 L6.2 4.6 L4.8 6.2 Q6 9 9.8 11.2 L11.4 9.8 L14.5 12 L13 14.5 Q6.5 14 1.5 3 Z" fill="#fff"/></svg>
      <svg viewBox="0 0 16 16" aria-label="Email"><rect x="1.5" y="3.5" width="13" height="9" fill="none" stroke="#fff" stroke-width="1.5"/><path d="M1.5 3.5 L8 9 L14.5 3.5" fill="none" stroke="#fff" stroke-width="1.5"/></svg>
      <svg viewBox="0 0 16 16" aria-label="News"><circle cx="8" cy="8" r="5.5" fill="#fff"/></svg>
      <svg viewBox="0 0 16 16" aria-label="Team"><rect x="2.5" y="2.5" width="11" height="11" fill="#fff"/></svg>
    </div>

    <ul class="contact-list">
      <li>+44 (0) 7700 900123</li>
      <li>daniel@brightmilldata.co.uk</li>
      <li>brightmilldata.co.uk/news</li>
      <li>brightmilldata.co.uk/team</li>
    </ul>

    <svg class="card-edge" viewBox="0 0 560 40" preserveAspectRatio="none">
      <path d="M0 30 H395 Q403 30 407 22 L410 16 Q414 8 424 8 H560 V40 H0 Z" fill="var(--orange)"/>
      <path d="M402 40 L409 24 Q415 14 427 14 H560 V40 Z" fill="var(--graphite)"/>
    </svg>
  </section>

</main>
</body>
</html>
```